International Clinical Software Company needs a new business card design

We are looking for a new business card design for our company that has recently expanded into the UK market, making us a multinational company.
After having rebranded our website and produced a new style guide, we are looking for a business card that is creative and attention grabbing, while being consistent with the style and colour scheme used on the new website, www.plumvora.example
We produce care management technology for the aged care market, but the main aspect we aim to communicate is the human element of our software, and the way it assists in providing better care for aged people, and stronger relationships between aged people and the staff that care for them.
Our current business card is a dark green with gold text, which makes the text quite difficult to read, not very aesthetically appealing and the colour scheme looks quite dated.
We would like something fresh and modern, that can still be colourful but doesn't use large blocks of dark colour, and uses the colours within our logo.
Something tying in with the leaves that are used in our logo could work quite nicely, along with the Autumn/Fall colours of soft greens, yellows and reds (also in our existing logo). However also happy to look at fresh, completely out of the box ideas we may not have yet considered.
Target Market(s)
The people that receive this business card work in the aged card or health industry and are either corporate/management level staff or clinical (Registered Nurses, care workers etc.)
Industry/Entity Type
Health Product
Contact Information for Business Card
Company Name - BrindlewayCare
Company locations: United Kingdom, Australia, New Zealand
Staff Details:
Staff name: Derek Mallow
Staff job title: Executive Chairman
Staff email: d.mallow@plumvora.example
Office phone number: 01742 918576
Font styles to use
Other font styles liked:
- Calibri
Requirements
Must have
- Must include the BrindlewayCare brand name in it's current font
- Must include logo (3 leaves in gold circle)
- Must include Business Card Details
Nice to have
- Elements of gold
- White space
- Something autumn themed but not too cliched
Should not have
- No blue - used by a major competitor and we would like to differentiate from them
- Large blocks of dark green colour (the green that appears in our leaves on the logo on our current business card is the background colour and it is far too dark)

```html
<!DOCTYPE html>
<html lang="en">
<head>
<meta charset="utf-8">
<title>BrindlewayCare Business Card</title>
<link href="https://fonts.googleapis.com/css2?family=Open+Sans:wght@400;600&display=swap" rel="stylesheet">
<style>
  :root {
    --gold: #b69d32;
    --gold-text: #b29a35;
    --white: #ffffff;
    --card-tint: #f4f3f1;
    --backdrop: #2e2e2e;
  }
  * { margin: 0; padding: 0; box-sizing: border-box; }
  html, body {
    width: 1200px;
    height: 900px;
    overflow: hidden;
    background: var(--backdrop);
    font-family: "Open Sans", sans-serif;
  }
  .business-card {
    position: absolute;
    left: 140px;
    top: 185px;
    width: 920px;
    height: 530px;
    border-radius: 38px;
    overflow: hidden;
    background: var(--white);
  }
  .leaf-texture {
    position: absolute;
    inset: 0;
    background: radial-gradient(ellipse at 40% 30%, var(--card-tint) 0%, var(--white) 70%);
  }
  .brand-band {
    position: absolute;
    left: 0;
    top: 292px;
    width: 392px;
    height: 160px;
    background: var(--gold);
  }
  .brand-mark {
    position: absolute;
    left: 160px;
    top: 22px;
    width: 72px;
    height: 72px;
    border-radius: 50%;
    background: var(--white);
  }
  .brand-name {
    position: absolute;
    left: 0;
    width: 392px;
    top: 104px;
    text-align: center;
    color: var(--white);
    font-size: 24px;
    font-weight: 400;
  }
  .person {
    position: absolute;
    left: 455px;
    top: 96px;
    color: var(--gold-text);
  }
  .person-name { font-size: 30px; font-weight: 400; line-height: 1.1; }
  .person-title { font-size: 18px; font-weight: 400; margin-top: 2px; }
  .contact-band {
    position: absolute;
    left: 485px;
    right: 0;
    top: 170px;
    height: 168px;
    background: var(--gold);
    color: var(--white);
    font-size: 19px;
  }
  .contact-row {
    position: absolute;
    left: 0;
    right: 0;
    display: flex;
    align-items: flex-start;
    gap: 14px;
    padding-left: 16px;
    line-height: 1.3;
  }
  .contact-row svg { flex: none; margin-top: 3px; }
  .row-address { top: 10px; }
  .row-phone { top: 92px; }
  .row-email { top: 134px; }
  .divider {
    position: absolute;
    left: 0;
    right: 0;
    height: 3px;
    background: var(--white);
  }
  .divider-one { top: 80px; }
  .divider-two { top: 124px; }
</style>
</head>
<body>
  <div class="business-card">
    <div class="leaf-texture" role="img" aria-label="Faint pale leaf and branch texture across the card"></div>

    <div class="brand-band">
      <div class="brand-mark"></div>
      <div class="brand-name">BrindlewayCare</div>
    </div>

    <div class="person">
      <div class="person-name">Derek Mallow</div>
      <div class="person-title">Executive Chairman</div>
    </div>

    <div class="contact-band">
      <div class="contact-row row-address">
        <svg width="22" height="20" viewBox="0 0 22 20" aria-hidden="true">
          <path d="M11 1 L21 10 H18 V19 H13 V13 H9 V19 H4 V10 H1 Z" fill="#ffffff"/>
        </svg>
        <div>BrindlewayCare<br>United Kingdom, Australia, New Zealand</div>
      </div>
      <div class="divider divider-one"></div>
      <div class="contact-row row-phone">
        <svg width="22" height="18" viewBox="0 0 22 18" aria-hidden="true">
          <path d="M2 6 C2 2 20 2 20 6 L20 8 L15 8 L15 6 L7 6 L7 8 L2 8 Z" fill="#ffffff"/>
          <rect x="5" y="9" width="12" height="8" rx="2" fill="#ffffff"/>
        </svg>
        <div>01742 918576</div>
      </div>
      <div class="divider divider-two"></div>
      <div class="contact-row row-email">
        <svg width="22" height="16" viewBox="0 0 22 16" aria-hidden="true">
          <rect x="1" y="1" width="20" height="14" fill="none" stroke="#ffffff" stroke-width="2"/>
          <path d="M1 1 L11 9 L21 1" fill="none" stroke="#ffffff" stroke-width="2"/>
        </svg>
        <div>d.mallow@plumvora.example</div>
      </div>
    </div>
  </div>
</body>
</html>
```